regPersonal Trainer Flyer Design

Project Deadline Extended
Reason: I have been very busy with other work and would like to extend the deadline to offer designers the chance to edit and improve designs with my help. Thank you for all the designs that have been sent so far.

```html
<!DOCTYPE html>
<html lang="en">
<head>
<meta charset="utf-8">
<title>Fitness Training – Personal Trainer Flyers</title>
<link rel="stylesheet" href="https://fonts.googleapis.com/css2?family=Ubuntu:wght@300;400;500;700&display=swap">
<style>
  :root {
    --stage: #dcdddf;
    --charcoal: #46494e;
    --blue: #1b5cab;
    --blue-deep: #124a90;
    --yellow: #f5c319;
    --white: #ffffff;
    --ink: #2a2c30;
    --panel: #eceef1;
    --photo-warm-a: #c98f78;
    --photo-warm-b: #6b5a58;
    --photo-cool-a: #d8d2cf;
    --photo-cool-b: #8a6d66;
  }
  * { margin: 0; padding: 0; box-sizing: border-box; }
  html, body { width: 1200px; height: 800px; overflow: hidden; }
  body {
    background: var(--stage);
    font-family: "Ubuntu", "Trebuchet MS", sans-serif;
    position: relative;
  }

  .flyer { position: absolute; overflow: hidden; box-shadow: 0 6px 18px rgba(0,0,0,.25); }
  .flyer__shapes { position: absolute; inset: 0; }
  .photo {
    position: absolute;
    background: linear-gradient(135deg, var(--photo-cool-a), var(--photo-warm-a) 55%, var(--photo-warm-b));
    border: 6px solid var(--white);
  }
  .photo--round { border-radius: 50%; }
  .photo--alt { background: linear-gradient(160deg, var(--photo-cool-a), var(--photo-cool-b)); }
  .photo--ring { box-shadow: 0 0 0 8px var(--yellow); }

  /* Portrait flyer */
  .flyer--portrait { left: 40px; top: 90px; width: 440px; height: 620px; background: var(--charcoal); }
  .title { position: absolute; line-height: 1; }
  .title__main { display: block; color: var(--yellow); font-weight: 700; }
  .title__sub { display: block; font-weight: 300; }
  .flyer--portrait .title { left: 92px; top: 58px; }
  .flyer--portrait .title__main { font-size: 66px; letter-spacing: -1px; }
  .flyer--portrait .title__sub { color: var(--white); font-size: 34px; letter-spacing: 5px; margin-top: 12px; margin-left: 4px; }

  .pitch {
    position: absolute;
    list-style: none;
    color: var(--white);
    font-weight: 500;
  }
  .pitch li { position: relative; padding-left: 16px; line-height: 1.25; }
  .pitch li::before {
    content: ""; position: absolute; left: 0; top: .38em;
    width: 9px; height: 9px; border-radius: 50%; background: var(--yellow);
  }
  .flyer--portrait .pitch { left: 268px; top: 228px; width: 170px; font-size: 13.5px; }

  .trainer { position: absolute; }
  .trainer__name { color: var(--yellow); font-weight: 500; }
  .trainer__role { color: var(--ink); font-weight: 400; }
  .flyer--portrait .trainer { left: 24px; top: 478px; }
  .flyer--portrait .trainer__name { font-size: 28px; }
  .flyer--portrait .trainer__role { font-size: 19px; margin-top: 2px; }

  .contact { position: absolute; color: var(--white); }
  .contact__phone { font-weight: 700; }
  .flyer--portrait .contact { left: 24px; top: 540px; }
  .flyer--portrait .contact__phone { font-size: 21px; letter-spacing: .5px; }
  .flyer--portrait .contact__email { font-size: 14px; margin-top: 2px; }

  .offer { position: absolute; text-align: center; color: var(--ink); font-size: 15px; line-height: 1.15; }
  .offer strong { font-weight: 700; }
  .flyer--portrait .offer { left: 278px; top: 548px; width: 110px; }

  /* Landscape flyer */
  .flyer--landscape { left: 520px; top: 200px; width: 640px; height: 392px; background: var(--blue); }
  .flyer--landscape .title { left: 34px; top: 206px; }
  .flyer--landscape .title__main { color: var(--blue); font-size: 40px; }
  .flyer--landscape .title__sub { color: var(--ink); font-size: 30px; letter-spacing: 2px; margin-top: 4px; }
  .flyer--landscape .pitch { left: 444px; top: 168px; width: 190px; font-size: 12.5px; }
  .flyer--landscape .pitch li::before { background: var(--white); width: 7px; height: 7px; }
  .flyer--landscape .offer { left: 284px; top: 198px; width: 82px; font-size: 16px; }
  .flyer--landscape .trainer { left: 34px; top: 306px; }
  .flyer--landscape .trainer__name { color: var(--blue); font-size: 24px; }
  .flyer--landscape .trainer__role { font-size: 17px; margin-top: 2px; }
  .flyer--landscape .contact { left: 440px; top: 304px; color: var(--ink); }
  .contact__row { display: flex; align-items: center; gap: 10px; }
  .flyer--landscape .contact__phone { font-size: 21px; }
  .flyer--landscape .contact__email { font-size: 13px; margin-top: 8px; }
  .icon { width: 16px; height: 16px; fill: var(--blue); flex: none; }
</style>
</head>
<body>

<!-- Portrait flyer -->
<section class="flyer flyer--portrait" aria-label="Portrait fitness training flyer">
  <svg class="flyer__shapes" viewBox="0 0 440 620" aria-hidden="true">
    <path d="M0,228 Q120,206 230,214 L230,236 Q110,230 0,254 Z" fill="var(--yellow)"/>
    <path d="M0,250 Q150,222 440,236 L440,620 L0,620 Z" fill="var(--blue)"/>
    <circle cx="348" cy="296" r="112" fill="var(--white)"/>
    <circle cx="348" cy="296" r="104" fill="var(--blue-deep)"/>
    <g transform="translate(332 568)">
      <polygon fill="var(--yellow)" points="58,0 48,13 50,29 35,35 29,50 13,48 0,58 -13,48 -29,50 -35,35 -50,29 -48,13 -58,0 -48,-13 -50,-29 -35,-35 -29,-50 -13,-48 0,-58 13,-48 29,-50 35,-35 50,-29 48,-13"/>
    </g>
  </svg>

  <h1 class="title"><span class="title__main">FITNESS</span><span class="title__sub">TRAINING</span></h1>

  <div class="photo photo--round" style="left:-14px;top:222px;width:132px;height:132px" role="img" aria-label="Trainer coaching a client on a weights bench"></div>
  <div class="photo photo--round photo--alt" style="left:92px;top:218px;width:140px;height:140px" role="img" aria-label="Trainer lifting a barbell in the gym"></div>
  <div class="photo photo--round" style="left:38px;top:310px;width:146px;height:146px" role="img" aria-label="Client working out on a chest press machine"></div>
  <div class="photo photo--round photo--alt photo--ring" style="left:166px;top:330px;width:118px;height:118px" role="img" aria-label="Client training on a gym machine"></div>
  <div class="photo photo--round" style="left:226px;top:388px;width:150px;height:150px" role="img" aria-label="Boxing pad session with a client"></div>
  <div class="photo photo--round photo--alt" style="left:186px;top:470px;width:116px;height:116px;border-color:var(--blue)" role="img" aria-label="Portrait of the personal trainer"></div>

  <ul class="pitch">
    <li>Lacking motivation?</li>
    <li>Not achieving your goals?</li>
    <li>Need help?</li>
    <li>Bored of the gym?</li>
    <li>You're never too old</li>
    <li>I can help improve your health and well-being</li>
  </ul>

  <div class="trainer">
    <p class="trainer__name">Dan Kerwell</p>
    <p class="trainer__role">Personal Trainer</p>
  </div>
  <div class="contact">
    <p class="contact__phone">07700 900418</p>
    <p class="contact__email">dankerwell@mailbox.co.uk</p>
  </div>
  <p class="offer">One Month<br><strong>Free</strong> Session</p>
</section>

<!-- Landscape flyer -->
<section class="flyer flyer--landscape" aria-label="Landscape fitness training flyer">
  <svg class="flyer__shapes" viewBox="0 0 640 392" aria-hidden="true">
    <path d="M0,160 L400,160 L360,300 L0,300 Z" fill="var(--panel)"/>
    <path d="M270,180 L390,180 L370,230 L390,282 L270,282 Z" fill="var(--yellow)"/>
    <rect x="0" y="300" width="640" height="66" fill="var(--yellow)"/>
    <rect x="0" y="366" width="640" height="26" fill="var(--charcoal)"/>
    <circle cx="330" cy="336" r="58" fill="var(--white)"/>
  </svg>

  <div class="photo" style="left:0;top:6px;width:112px;height:96px" role="img" aria-label="Trainer coaching a client"></div>
  <div class="photo photo--alt" style="left:114px;top:4px;width:118px;height:80px" role="img" aria-label="Client on a chest press machine"></div>
  <div class="photo" style="left:234px;top:6px;width:128px;height:70px" role="img" aria-label="Trainer lifting a barbell"></div>
  <div class="photo photo--alt" style="left:364px;top:4px;width:104px;height:78px" role="img" aria-label="Trainer at the weights rack"></div>
  <div class="photo" style="left:470px;top:4px;width:170px;height:116px" role="img" aria-label="Client training with a cable machine"></div>
  <div class="photo photo--alt" style="left:0;top:104px;width:116px;height:78px" role="img" aria-label="Client stretching in the gym"></div>
  <div class="photo" style="left:150px;top:80px;width:148px;height:110px" role="img" aria-label="Boxing pad session with a client"></div>
  <div class="photo photo--round photo--alt" style="left:280px;top:286px;width:100px;height:100px;border-color:var(--blue)" role="img" aria-label="Portrait of the personal trainer"></div>

  <h2 class="title"><span class="title__main">FITNESS</span><span class="title__sub">TRAINING</span></h2>
  <p class="offer">One Month<br><strong>Free</strong><br>Session</p>

  <ul class="pitch">
    <li>Lacking motivation?</li>
    <li>Not achieving your goals?</li>
    <li>Need help?</li>
    <li>Bored of the gym?</li>
    <li>You're never too old</li>
    <li>I can help improve your health and well-being</li>
  </ul>

  <div class="trainer">
    <p class="trainer__name">Dan Kerwell</p>
    <p class="trainer__role">Personal Trainer</p>
  </div>
  <div class="contact">
    <p class="contact__row contact__phone">
      <svg class="icon" viewBox="0 0 24 24" aria-hidden="true"><path d="M6.6 10.8a15.1 15.1 0 0 0 6.6 6.6l2.2-2.2a1 1 0 0 1 1-.25 11.4 11.4 0 0 0 3.6.57 1 1 0 0 1 1 1V20a1 1 0 0 1-1 1A17 17 0 0 1 3 4a1 1 0 0 1 1-1h3.5a1 1 0 0 1 1 1c0 1.25.2 2.45.57 3.57a1 1 0 0 1-.25 1z"/></svg>
      07700 900418
    </p>
    <p class="contact__row contact__email">
      <svg class="icon" viewBox="0 0 24 24" aria-hidden="true"><path d="M2 5h20v14H2z" opacity=".9"/><path d="M2 5l10 8 10-8" fill="none" stroke="#fff" stroke-width="1.8"/></svg>
      dankerwell@mailbox.co.uk
    </p>
  </div>
</section>

</body>
</html>
```